Dovecote Realty

Business cards for 4 people

They need to say for all
87 Tarrow Quay, Boston MA 02114

Each person will have their own personal information
We would like gold embossing for the name of the company
Marla is the blonde sitting in the chair smiling her information should be on the back of the card with her name and information
Should say for slogan classic pattern, elevated experience
marla@dovecoteprops.com
(413) 555-0182

Odette is the brunette with wavy hair in the tan suit celina@dovecoteprops.com
(617) 555-0137

faith@dovecoteprops.com
(413) 555-0164
standing next to the chair

hope@dovecoteprops.com
(413) 555-0199
close up headshot

```html
<!DOCTYPE html>
<html lang="en">
<head>
<meta charset="utf-8">
<title>Dovecote Realty – Business Card</title>
<link rel="stylesheet" href="https://fonts.googleapis.com/css2?family=Montserrat:wght@400;500;700&display=swap">
<style>
  :root {
    --navy-deep: #1e2b4a;
    --navy-light: #5c6b85;
    --gold: #d9ab5c;
    --paper: #ececec;
    --white: #ffffff;
    --stage-light: #f2f2f2;
    --stage-dark: #c9c9c9;
  }
  * { box-sizing: border-box; margin: 0; padding: 0; }
  html, body { width: 1200px; height: 1200px; overflow: hidden; }
  body {
    background: linear-gradient(135deg, var(--stage-light), var(--stage-dark));
    font-family: "Montserrat", sans-serif;
    position: relative;
  }
  .card {
    position: absolute;
    left: 150px;
    width: 900px;
    height: 514px;
    border-radius: 26px;
    overflow: hidden;
    box-shadow: 0 10px 28px rgba(0,0,0,0.22);
  }
  .card--front {
    top: 60px;
    background: linear-gradient(110deg, var(--navy-light) 0%, #3d4c6b 40%, var(--navy-deep) 85%);
  }
  .card--back {
    top: 626px;
    background: linear-gradient(110deg, var(--navy-light) 0%, #34425f 35%, var(--navy-deep) 65%);
  }

  /* Front */
  .brand-mark {
    position: absolute;
    left: 150px; top: 150px;
    width: 100px; height: 100px;
    border: 3px solid var(--gold);
    border-radius: 50%;
  }
  .brand-name {
    position: absolute;
    right: 110px; top: 300px;
    color: var(--gold);
    font-weight: 500;
    font-size: 40px;
    letter-spacing: 3px;
    text-transform: uppercase;
  }

  /* Back */
  .back-shapes { position: absolute; inset: 0; width: 100%; height: 100%; }
  .portrait { position: absolute; left: 595px; top: 105px; width: 290px; height: 290px; }
  .identity { position: absolute; left: 68px; top: 64px; }
  .identity__name { color: var(--gold); font-weight: 700; font-size: 38px; }
  .identity__title { color: var(--white); font-weight: 500; font-size: 21px; margin-top: 4px; }
  .address {
    position: absolute; left: 68px; top: 268px;
    color: var(--white); font-size: 21px; line-height: 1.4; font-style: normal;
  }
  .contacts {
    position: absolute; left: 68px; top: 360px;
    list-style: none; color: var(--white); font-size: 21px;
  }
  .contacts li { display: flex; align-items: center; gap: 14px; height: 34px; }
  .contacts svg { width: 20px; height: 20px; flex: none; }
</style>
</head>
<body>

<section class="card card--front" aria-label="Business card front">
  <span class="brand-mark" aria-hidden="true"></span>
  <span class="brand-name">Dovecote Realty</span>
</section>

<section class="card card--back" aria-label="Business card back">
  <svg class="back-shapes" viewBox="0 0 900 514" aria-hidden="true">
    <circle cx="900" cy="160" r="380" fill="#ffffff"/>
    <circle cx="900" cy="160" r="370" fill="#d9ab5c"/>
    <circle cx="900" cy="160" r="345" fill="#1e2b4a"/>
    <circle cx="900" cy="160" r="330" fill="#ececec"/>
  </svg>

  <svg class="portrait" viewBox="0 0 290 290" role="img" aria-label="Portrait photo of Marla Fenwick">
    <defs>
      <radialGradient id="portraitTone" cx="0.5" cy="0.45" r="0.6">
        <stop offset="0" stop-color="#b79a8c"/>
        <stop offset="0.55" stop-color="#4a3b35"/>
        <stop offset="1" stop-color="#1c1f2b"/>
      </radialGradient>
    </defs>
    <circle cx="145" cy="145" r="145" fill="url(#portraitTone)"/>
  </svg>

  <div class="identity">
    <h1 class="identity__name">Marla Fenwick</h1>
    <p class="identity__title">Founder &amp; Director</p>
  </div>

  <address class="address">
    87 Tarrow Quay, Boston,<br>MA 02114, United States
  </address>

  <ul class="contacts">
    <li>
      <svg viewBox="0 0 24 24" aria-hidden="true"><path fill="#d9ab5c" d="M6.6 10.8a15 15 0 0 0 6.6 6.6l2.2-2.2c.3-.3.7-.4 1-.2 1.1.4 2.3.6 3.6.6.6 0 1 .4 1 1V20c0 .6-.4 1-1 1A17 17 0 0 1 3 4c0-.6.4-1 1-1h3.5c.6 0 1 .4 1 1 0 1.3.2 2.5.6 3.6.1.3 0 .7-.2 1z"/></svg>
      (413) 555-0182
    </li>
    <li>
      <svg viewBox="0 0 24 24" aria-hidden="true"><rect x="2" y="5" width="20" height="14" rx="1.5" fill="#d9ab5c"/><path d="M3 6l9 7 9-7" fill="none" stroke="#1e2b4a" stroke-width="1.6"/></svg>
      marla@dovecoteprops.com
    </li>
    <li>
      <svg viewBox="0 0 24 24" aria-hidden="true"><circle cx="12" cy="12" r="10" fill="#d9ab5c"/><path d="M2 12h20M12 2c3 3 3 17 0 20M12 2c-3 3-3 17 0 20" fill="none" stroke="#1e2b4a" stroke-width="1.4"/></svg>
      www.dovecoteprops.com
    </li>
  </ul>
</section>

</body>
</html>
```